Business Card Design

We need a business card designed for our new company. Prefer a black card with white logo & writing.

Contact Information for Business Card

Ted Galloway, address: 7-4812 Fernhollow Road, Abbotsford, BC, V3K 8R2, Office Phone: 604-712-3390, Cell: 604-947-2164, Email: ted@resinworkshub.ca

Colors

Designer to choose only greyscale colors for use in the design.

```html
<!DOCTYPE html>
<html lang="en">
<head>
<meta charset="utf-8">
<title>Resin Works Hub — Business Card</title>
<link href="https://fonts.googleapis.com/css2?family=Poppins:wght@300;400;700&display=swap" rel="stylesheet">
<style>
  :root {
    --backdrop: #232323;
    --card: #1f1f21;
    --ink: #ffffff;
    --ink-soft: #e6e6e6;
    --back-mark: #9a9a9e;
    --icon-glyph: #1f1f21;
  }
  * { margin: 0; padding: 0; box-sizing: border-box; }
  html, body {
    width: 1200px; height: 780px; overflow: hidden;
    background: var(--backdrop);
    font-family: "Poppins", sans-serif;
  }
  .sheet {
    position: relative; width: 1200px; height: 780px;
    display: flex; align-items: center; justify-content: center; gap: 50px;
  }
  .card {
    position: relative; width: 530px; height: 303px;
    background: var(--card);
    box-shadow: 0 10px 30px rgba(0,0,0,0.5);
  }
  /* Front */
  .identity {
    position: absolute; left: 0; top: 46px;
    padding-left: 42px;
  }
  .identity-bar {
    position: absolute; left: 20px; top: 4px;
    width: 11px; height: 46px; background: var(--ink);
  }
  .person-name {
    color: var(--ink); font-size: 27px; line-height: 1; font-weight: 300;
  }
  .person-name .first { font-weight: 700; }
  .person-title {
    color: var(--ink-soft); font-size: 12.5px; font-weight: 400; margin-top: 4px;
  }
  .address {
    position: absolute; left: 42px; top: 142px;
    color: var(--ink-soft); font-size: 12.5px; line-height: 1.4; font-weight: 300;
  }
  .contacts {
    position: absolute; left: 42px; top: 196px; list-style: none;
    color: var(--ink-soft); font-size: 12.5px; font-weight: 300;
  }
  .contacts li { display: flex; align-items: center; gap: 8px; height: 19px; }
  .contacts svg { width: 13px; height: 13px; flex: none; }
  .brand-front {
    position: absolute; right: 36px; top: 0; bottom: 0;
    display: flex; align-items: center;
    color: var(--ink); font-size: 32px; font-weight: 700; letter-spacing: 0.5px;
    line-height: 1.05; text-align: left; width: 200px;
  }
  /* Back */
  .brand-back {
    position: absolute; inset: 0;
    display: flex; align-items: center; justify-content: center;
    color: var(--back-mark); font-size: 44px; font-weight: 700; letter-spacing: 0.5px;
  }
</style>
</head>
<body>
<main class="sheet">
  <section class="card card-front" aria-label="Card front">
    <div class="identity">
      <span class="identity-bar"></span>
      <h1 class="person-name"><span class="first">Ted</span> Galloway</h1>
      <p class="person-title">Founder &amp; CEO</p>
    </div>
    <p class="address">7-4812 Fernhollow Road,<br>Abbotsford, BC, V3K 8R2.</p>
    <ul class="contacts">
      <li>
        <svg viewBox="0 0 16 16"><circle cx="8" cy="8" r="8" fill="#fff"/><path d="M5 4.5c.6-.4 1.1-.3 1.4.2l.6 1.1c.2.4.1.8-.3 1.1l-.4.3c.4 1 1.2 1.8 2.2 2.2l.3-.4c.3-.4.7-.5 1.1-.3l1.1.6c.5.3.6.8.2 1.4-.5.7-1.3 1-2.200.6C7 10.5 5.5 9 4.7 7c-.4-.9-.1-1.8.3-2.5z" fill="var(--icon-glyph)"/></svg>
        604-712-3390
      </li>
      <li>
        <svg viewBox="0 0 16 16"><rect width="16" height="16" rx="2" fill="#fff"/><rect x="5.5" y="3" width="5" height="10" rx="1" fill="none" stroke="var(--icon-glyph)" stroke-width="1.2"/><circle cx="8" cy="11.3" r=".6" fill="var(--icon-glyph)"/></svg>
        604-947-2164
      </li>
      <li>
        <svg viewBox="0 0 16 16"><circle cx="8" cy="8" r="8" fill="#fff"/><circle cx="8" cy="8" r="5" fill="none" stroke="var(--icon-glyph)" stroke-width="1"/><ellipse cx="8" cy="8" rx="2.2" ry="5" fill="none" stroke="var(--icon-glyph)" stroke-width="1"/><path d="M3 8h10" stroke="var(--icon-glyph)" stroke-width="1"/></svg>
        www.resinworkshub.ca
      </li>
      <li>
        <svg viewBox="0 0 16 16"><rect width="16" height="16" rx="2" fill="#fff"/><rect x="3" y="4.5" width="10" height="7" fill="none" stroke="var(--icon-glyph)" stroke-width="1.1"/><path d="M3 4.5l5 4 5-4" fill="none" stroke="var(--icon-glyph)" stroke-width="1.1"/></svg>
        ted@resinworkshub.ca
      </li>
    </ul>
    <p class="brand-front">Resin Works Hub</p>
  </section>

  <section class="card card-back" aria-label="Card back">
    <p class="brand-back">Resin Works Hub</p>
  </section>
</main>
</body>
</html>
```